Graduates Society Sponsorship Brochure

The University of Glenmarrow Graduates Society of New York is putting together a brochure to solicit corporate sponsors for our 5th annual black tie gala in downtown Manhattan.
The Graduates Society works to benefit both the alumni community and to give back to the University. Our Thistle Soirée seeks to bring together former students, friends, and family of Glenmarrow to remind them of their own Thistle Soirée experience during university. We are also promoting Scottish-American relations, and want to make clear to sponsors the benefit of access to our demographic.

Target Market(s)

Corporations, Special Interest Groups, parties with affiliation to Scotland and the UK.

Industry/Entity Type

Non-Profit

Font styles to use
Serif

Colors
ec1f27
0255a3

Requirements
Must have
• Clear details about the separation of sponsorship price points, emphasis on the potential impact and benefit of partnership.
Nice to have
• Some big pictures and lots of icons to show the different sponsorship levels.

```html
<!DOCTYPE html>
<html lang="en">
<head>
<meta charset="utf-8">
<title>Thistle Soirée Sponsorship Brochure – Cover</title>
<link rel="stylesheet" href="https://fonts.googleapis.com/css2?family=Cormorant+Garamond:wght@500;600;700&display=swap">
<style>
  :root {
    --backdrop: #0a7fc0;
    --backdrop-deep: #0a67a0;
    --page-light: #ffffff;
    --page-shade: #e2e3e6;
    --ink: #141414;
    --ink-soft: #1e1e1e;
    --gold: #e3b94e;
    --gold-light: #f6d77c;
    --gold-deep: #a8751f;
  }
  * { margin: 0; padding: 0; box-sizing: border-box; }
  html, body { width: 1200px; height: 1000px; overflow: hidden; }
  body {
    background: linear-gradient(135deg, var(--backdrop) 0%, var(--backdrop-deep) 100%);
    font-family: "Cormorant Garamond", Georgia, serif;
    position: relative;
  }
  .spread {
    position: absolute;
    left: 139px; top: 174px;
    width: 922px; height: 651px;
    display: flex;
  }
  .back-page {
    position: relative;
    width: 461px; height: 651px;
    background: linear-gradient(180deg, var(--page-light) 0%, var(--page-shade) 100%);
  }
  .address-band {
    position: absolute;
    left: 0; top: 540px;
    width: 461px; height: 89px;
    background: var(--ink);
    border-top: 3px solid var(--gold);
    border-bottom: 3px solid var(--gold);
    text-align: center;
    color: var(--gold-light);
    font-weight: 600;
    font-size: 29px;
    line-height: 38px;
    padding-top: 6px;
  }
  .address-band::before,
  .address-band::after {
    content: "";
    position: absolute;
    left: 224px;
    width: 12px; height: 12px;
    background: var(--gold-light);
    transform: rotate(45deg);
  }
  .address-band::before { top: -8px; }
  .address-band::after { bottom: -8px; }

  .front-page {
    position: relative;
    width: 461px; height: 651px;
    background: radial-gradient(ellipse at 50% 20%, #2a2a2a 0%, var(--ink) 70%);
    color: var(--gold);
    text-align: center;
    overflow: hidden;
  }
  .front-art { position: absolute; inset: 0; }
  .event-title {
    position: absolute;
    top: 52px; left: 0; right: 0;
    font-weight: 700;
    font-size: 52px;
    line-height: 62px;
    color: var(--gold);
  }
  .event-title sup { font-size: 28px; vertical-align: 20px; margin-right: 2px; }
  .event-mark {
    position: absolute;
    top: 270px; left: 0; right: 0;
    color: var(--gold);
    font-weight: 700;
  }
  .event-mark .mark-dot {
    display: block;
    width: 34px; height: 34px;
    margin: 0 auto 8px;
    border-radius: 50%;
    background: var(--gold);
  }
  .event-mark .mark-name { display: block; font-size: 34px; line-height: 38px; }
  .event-mark .mark-year { display: block; font-size: 24px; line-height: 30px; }
  .organiser {
    position: absolute;
    top: 484px; left: 0; right: 0;
    font-weight: 600;
    font-size: 17px;
    line-height: 22px;
    color: var(--gold);
  }
  .divider {
    position: absolute;
    top: 540px; left: 120px;
    width: 221px; height: 10px;
  }
  .doc-type {
    position: absolute;
    top: 556px; left: 0; right: 0;
    font-weight: 600;
    font-size: 34px;
    line-height: 42px;
    color: var(--gold);
  }
</style>
</head>
<body>
  <main class="spread">
    <section class="back-page">
      <div class="address-band">
        <p>Suite 2407</p>
        <p>New York, NY.</p>
      </div>
    </section>

    <section class="front-page">
      <svg class="front-art" width="461" height="651" viewBox="0 0 461 651" aria-hidden="true">
        <defs>
          <linearGradient id="goldSweep" x1="0" y1="0" x2="1" y2="0">
            <stop offset="0" stop-color="#a8751f"/>
            <stop offset="0.45" stop-color="#f6d77c"/>
            <stop offset="1" stop-color="#b98226"/>
          </linearGradient>
        </defs>
        <path d="M0,150 C150,228 310,252 461,176 L461,190 C310,258 150,240 0,186 Z" fill="url(#goldSweep)"/>
        <path d="M21,214 Q230,272 440,214 L440,466 Q230,404 21,466 Z" fill="#181818" stroke="#e3b94e" stroke-width="2"/>
        <path d="M0,478 Q230,410 461,490 L461,502 Q230,428 0,500 Z" fill="url(#goldSweep)"/>
      </svg>

      <h1 class="event-title"><sup>5th</sup>Annual<br>Thistle Soirée</h1>

      <div class="event-mark">
        <span class="mark-dot"></span>
        <span class="mark-name">THISTLE SOIRÉE</span>
        <span class="mark-year">2018</span>
      </div>

      <p class="organiser">University of Glenmarrow<br>Graduates Society of New York</p>

      <svg class="divider" width="221" height="10" viewBox="0 0 221 10" aria-hidden="true">
        <line x1="0" y1="5" x2="100" y2="5" stroke="#e3b94e" stroke-width="1.5"/>
        <rect x="106" y="1" width="8" height="8" fill="#e3b94e" transform="rotate(45 110 5)"/>
        <line x1="121" y1="5" x2="221" y2="5" stroke="#e3b94e" stroke-width="1.5"/>
      </svg>

      <h2 class="doc-type">Sponsorship<br>Brochure</h2>
    </section>
  </main>
</body>
</html>
```